Corvane Business Cards

Front of business card will have logo, name, address, & telephone number. Back of card will have a list of services provided - Roads, Substation Pads, Temporary Pads, Site Pads, Land Leveling, Powerline Row Cleaning, Land Clearing, Gates, Fencing, Construction Entrances, Excavation, Trenching, Underground Utilities, Directional Boring, Pile Driving. We are a construction company that uses heavy equipment like bulldozers, motor graders/blades, dump trucks, backhoes, hydro axes, & skid loaders. We build roads, pads, & install electric utility lines & waterlines underground. This logo is new. The word "Construction" can be smaller as uploaded 2 example edited logos. We will be using this card design for many employees.
Target Market(s)
Industrial Electric Powerline, Wind Turbine, Solar Panel, & Water Utility companies.
Contact Information for Business Card
Name/Position - Dwayne Halster - Owner
Address: 4875 FM 309
Harlow, TX 79412
Phone number - (325) 482-5096

```html
<!DOCTYPE html>
<html lang="en">
<head>
<meta charset="utf-8">
<title>Corvane Construction – Business Card</title>
<link rel="stylesheet" href="https://fonts.googleapis.com/css2?family=Montserrat:wght@400;500;700&display=swap">
<style>
  :root {
    --maroon: #3d0b17;
    --maroon-ink: #4a1220;
    --paper: #ffffff;
    --stage: #e6e4e4;
    --on-maroon: #ffffff;
  }
  * { box-sizing: border-box; margin: 0; padding: 0; }
  html, body {
    width: 1200px; height: 900px; overflow: hidden;
    background: var(--stage);
    font-family: "Montserrat", sans-serif;
  }
  .canvas {
    width: 1200px; height: 900px;
    display: flex; flex-direction: column; align-items: center; justify-content: center;
    gap: 48px;
  }
  .card {
    width: 700px; height: 400px;
    position: relative;
    box-shadow: 0 6px 18px rgba(0,0,0,.18);
  }

  /* Front */
  .card-front {
    background: var(--paper);
    color: var(--maroon-ink);
    display: flex; align-items: center;
    padding: 0 48px;
  }
  .brand { flex: none; }
  .brand-mark { display: flex; align-items: center; gap: 12px; }
  .brand-square { flex: none; width: 22px; height: 22px; background: var(--maroon); }
  .brand-name {
    font-weight: 500; letter-spacing: 2px; line-height: 1.05;
    color: var(--maroon); white-space: nowrap;
  }
  .card-front .brand-name { font-size: 32px; }
  .brand-sub { font-size: 20px; display: block; letter-spacing: 3px; }
  .divider { flex: none; width: 2px; height: 170px; background: var(--maroon); margin: 0 36px; }
  .contact { display: flex; flex-direction: column; gap: 6px; white-space: nowrap; }
  .contact-name { font-size: 22px; font-weight: 700; letter-spacing: 1px; text-transform: uppercase; }
  .contact-role { font-size: 16px; margin-bottom: 12px; }
  .contact-line { display: flex; align-items: flex-start; gap: 10px; font-size: 18px; font-weight: 500; line-height: 1.3; }
  .contact-line svg { flex: none; margin-top: 3px; }

  /* Back */
  .card-back {
    background: var(--maroon);
    color: var(--on-maroon);
    padding: 40px 44px;
  }
  .card-back .brand-mark { justify-content: flex-end; gap: 16px; }
  .card-back .brand-name { color: var(--on-maroon); font-size: 40px; text-align: right; }
  .card-back .brand-square { background: var(--on-maroon); width: 26px; height: 26px; }
  .services { margin-top: 36px; display: flex; gap: 24px; }
  .services-title { font-size: 16px; font-weight: 700; margin-bottom: 4px; }
  .service-list { list-style: none; font-size: 15px; line-height: 1.6; white-space: nowrap; }
  .service-list li::before { content: "•"; margin-right: 8px; }
  .col-first { width: 120px; flex: none; }
  .col-second { width: 170px; flex: none; padding-top: 26px; }
  .col-third { padding-top: 26px; }
</style>
</head>
<body>
<main class="canvas">

  <section class="card card-front" aria-label="Business card front">
    <div class="brand">
      <div class="brand-mark">
        <span class="brand-square"></span>
        <span class="brand-name">CORVANE<span class="brand-sub">CONSTRUCTION</span></span>
      </div>
    </div>
    <div class="divider"></div>
    <div class="contact">
      <p class="contact-name">Dwayne Halster</p>
      <p class="contact-role">owner</p>
      <p class="contact-line">
        <svg width="16" height="18" viewBox="0 0 16 18" aria-hidden="true"><path d="M4 1 L7 5 L5 7 Q7 11 10 13 L12 11 L15 14 L13 17 Q6 16 2 8 Q1 4 4 1 Z" fill="currentColor"/></svg>
        (325) 482-5096
      </p>
      <p class="contact-line">
        <svg width="16" height="20" viewBox="0 0 16 20" aria-hidden="true"><path d="M8 1 A6.5 6.5 0 0 1 14.5 7.5 C14.5 12 8 19 8 19 C8 19 1.5 12 1.5 7.5 A6.5 6.5 0 0 1 8 1 Z" fill="currentColor"/><circle cx="8" cy="7.5" r="2.4" fill="#fff"/></svg>
        <span>4875 FM 309<br>Harlow, TX 79412</span>
      </p>
    </div>
  </section>

  <section class="card card-back" aria-label="Business card back">
    <div class="brand-mark">
      <span class="brand-square"></span>
      <span class="brand-name">CORVANE<br>CONSTRUCTION</span>
    </div>
    <div class="services">
      <div class="col-first">
        <p class="services-title">Services:</p>
        <ul class="service-list">
          <li>Roads</li><li>Site Pads</li><li>Gates</li><li>Fencing</li>
        </ul>
      </div>
      <ul class="service-list col-second">
        <li>Trenching</li><li>Temporary Pads</li><li>Land Leveling</li><li>Land Clearing</li><li>Substation Pads</li>
      </ul>
      <ul class="service-list col-third">
        <li>Powerline Row Cleaning</li><li>Construction Entrances</li><li>Excavation</li><li>Underground Utilities</li><li>Directional Boring, Pile Driving</li>
      </ul>
    </div>
  </section>

</main>
</body>
</html>
```